Wordpress Design Project for Bankruptcy Law Office in San Francisco

our current website: www.dorvanelilaw-example.com

we would like to re-design it for wordpress to make it faster and a bit more modern.

content should be similar to what we have there right now but also we do family law

please include logo for law office:

Law Office of Marta K. Dolvenidze

Thank you.
Updates

please see attached word document with logos that we like as an example.

we do tend to like color red.  darker red.

Please submit your design variations and logo as soon as possible.   We would like to go over them and make our decision

Reason: Please create couple of more variations of logo for your design, so we can make our decision what we like the most. Please see word doc for samples: Text: Law Office Of Marta K. Dolvenidze

Reason: final touches

Target Market(s)

bankruptcy and family law clients

Industry/Entity Type

Family Law

Requirements
Must have
• see examples of law sites
http://promo.lexorbin-example.com/testimonials

- new logo: Law Office of Marta K. Dolvenidze
- client intake form
- blog
- contact us form

Nice to have
• - map
- red color
- on the front page a nice photo of SF or a happy family

```html
<!DOCTYPE html>
<html lang="en">
<head>
<meta charset="utf-8">
<title>Law Office of Marta K. Dolvenidze</title>
<link rel="stylesheet" href="https://fonts.googleapis.com/css2?family=Cinzel:wght@400&family=Oswald:wght@400&family=PT+Sans:wght@400;700&family=Rokkitt:wght@500;700&family=Arimo:wght@400;700&display=swap">
<style>
:root{
  --bg:#d6d6d6;
  --red:#b0151c;
  --red-dark:#7a0a0f;
  --nav:#4e0507;
  --heading:#5a0a0e;
  --text:#222;
  --panel:#3b3b3b;
  --footer:#464646;
  --field:#e6e6e6;
  --green:#3a9a1c;
  --yellow:#ffe94a;
}
*{margin:0;padding:0;box-sizing:border-box}
html,body{width:1096px;height:1200px;overflow:hidden}
body{background:linear-gradient(135deg,#e2e2e2,#cfcfcf 50%,#dcdcdc);font-family:"PT Sans",sans-serif;color:var(--text);position:relative}
.page{position:absolute;left:105px;top:18px;width:886px;height:1157px;background:#fff;box-shadow:0 0 12px rgba(0,0,0,.35)}
.header{position:absolute;left:0;top:0;width:886px;height:99px;background:linear-gradient(180deg,#c3232a,#9e1217);overflow:hidden}
.header-deco{position:absolute;right:0;top:0;width:260px;height:99px;background:linear-gradient(90deg,rgba(158,18,23,0),rgba(120,20,20,.6))}
.logo{position:absolute;left:21px;top:20px;width:400px;font-family:"Cinzel",serif;font-weight:400;color:#fff;line-height:1}
.logo .line1{display:flex;align-items:center;gap:8px;font-size:22px;letter-spacing:1px;white-space:nowrap}
.logo .line1::before,.logo .line1::after{content:"";flex:1;height:1px;background:#fff;margin-top:8px}
.logo .line2{display:block;font-size:32px;margin-top:9px;letter-spacing:1px;white-space:nowrap}
.phone{position:absolute;left:698px;top:24px;display:flex;align-items:center;gap:6px;color:#fff;font-family:"Cinzel",serif;font-size:21px;letter-spacing:1px}
.nav{position:absolute;left:0;top:99px;width:886px;height:40px;background:var(--nav)}
.nav a{position:absolute;top:10px;transform:translateX(-50%);color:#fff;text-decoration:none;font-family:"Oswald",sans-serif;font-size:15px;white-space:nowrap;letter-spacing:-.2px}
.panel{position:absolute;left:17px;width:221px;background:var(--panel);outline:1px dashed #888;outline-offset:-3px;border:2px solid #555;color:#fff}
.panel h2{font-family:"PT Sans",sans-serif;font-weight:400;font-size:15.5px;margin:12px 0 0 12px;letter-spacing:.2px}
.info{top:159px;height:253px}
.info h3{font-weight:400;font-size:15px;margin:17px 0 0 12px}
.info .photo{display:block;margin:6px 0 0 13px;width:190px;height:76px;background:linear-gradient(180deg,#d9c7b8,#9a8a7a);border:1px solid #ccc}
.info p{font-family:"Arimo",sans-serif;font-size:9.6px;line-height:13.7px;color:#ccc;margin:8px 12px 0 14px;text-align:justify}
.contact{top:434px;height:305px}
.contact .req{font-size:12px;margin:18px 0 0 20px}
.field{display:block;margin:0 0 0 13px;width:187px;height:24px;border-radius:3px;background:linear-gradient(180deg,#f2f2f2,#cfcfcf);color:#777;font-size:11.5px;padding:5px 7px}
.field.first{margin-top:9px}
.field+.field{margin-top:9px}
.field.msg{height:64px}
.submit{position:absolute;left:150px;bottom:-1px;width:66px;height:24px;background:linear-gradient(180deg,#4fb028,#2d8510);color:#fff;font-size:11.5px;text-align:center;line-height:24px;border-radius:2px 2px 0 0}
.hero{position:absolute;left:255px;top:159px;width:615px;height:255px;background:linear-gradient(90deg,#8f9aa5,#c6cbd0 45%,#6a6f75 80%,#3c3f44);overflow:hidden}
.hero-tag{position:absolute;left:0;top:71px;width:356px;height:110px;background:rgba(52,55,66,.95);color:#fff;font-family:"Rokkitt",serif;line-height:1;overflow:hidden}
.hero-tag span{position:absolute;right:10px;white-space:nowrap;transform:scaleX(.78);transform-origin:right center}
.hero-tag .a{top:10px;font-size:36px;font-weight:500}
.hero-tag .b{top:54px;font-size:43px;font-weight:700;letter-spacing:.3px}
.dots{position:absolute;left:337px;top:241px;display:flex;gap:4px}
.dots span{width:8px;height:8px;border-radius:50%;background:#e8c24c}
.dots span:last-child{background:#f4f0e0;width:10px;height:10px;margin-top:-1px}
.main{position:absolute;left:255px;top:440px;width:615px}
.main h1{font-size:18px;font-weight:700;color:var(--heading);letter-spacing:-.1px}
.main p{font-size:12.2px;line-height:20px;margin:8px 0 0 2px;text-align:justify}
.main p+p{margin-top:20px}
.main h2{font-size:16.5px;color:var(--heading);margin:14px 0 0 2px;font-weight:700}
.main h2+p{margin-top:0}
.card{position:absolute;top:761px;width:272px;height:222px;border-radius:6px 6px 0 0;background:linear-gradient(180deg,#e0001a,#c30015 60%,#b00012);color:#fff;box-shadow:0 8px 8px -4px rgba(0,0,0,.45)}
.card h2{font-family:"PT Sans",sans-serif;font-weight:400;font-size:31px;margin:11px 0 0 19px;letter-spacing:-.5px;line-height:1.1;white-space:nowrap}
.card h2.small{font-size:24px;margin-top:17px}
.card .photo{position:absolute;left:21px;top:51px;width:229px;height:58px;background:linear-gradient(90deg,#c9ccd0,#d8b8a4 40%,#b8a090 70%,#c6cacf)}
.card p{position:absolute;left:19px;top:114px;width:233px;font-family:"Arimo",sans-serif;font-size:10.8px;line-height:14.6px;text-align:justify}
.card .more{position:absolute;right:11px;bottom:12px;font-family:"Arimo",sans-serif;font-size:10.8px;font-weight:700;color:var(--yellow)}
.footer{position:absolute;left:0;top:1025px;width:886px;height:132px;background:var(--footer);color:#fff;font-family:"Arimo",sans-serif;font-size:10.8px}
.footer .links{position:absolute;left:20px;top:15px;word-spacing:1px}
.footer .links span{margin-right:12px}
.footer .disclaimer{position:absolute;left:20px;top:48px;width:620px;line-height:16.4px}
.badge{position:absolute;left:770px;top:26px;width:93px;height:75px}
.badge::after{content:"";position:absolute;left:10px;top:9px;width:93px;height:75px;background:#7a7a7a;z-index:0}
.badge::before{content:"";position:absolute;inset:0;background:#fff;z-index:1;border:4px solid #fff;box-shadow:inset 0 0 0 1px #aaa}
</style>
</head>
<body>
<div class="page">
  <header class="header">
    <div class="header-deco"></div>
    <div class="logo"><span class="line1">LAW OFFICE OF</span><span class="line2">MARTA K. DOLVENIDZE</span></div>
    <div class="phone">
      <svg width="24" height="24" viewBox="0 0 24 24" aria-hidden="true"><rect width="24" height="24" rx="4" fill="#fff"/><path d="M8 5c1 0 2 3 2 4s-1.5 1.5-1 3 2 3 3 3.5 1.5-1 2.5-1 3.5 1.5 3.5 2.5-2 2.5-3.5 2.5C10 19.5 5 14 5 9c0-2 2-4 3-4z" fill="#b0151c"/></svg>
      <span>415-555-0147</span>
    </div>
  </header>
  <nav class="nav">
    <a href="#" style="left:91px">HOME</a>
    <a href="#" style="left:198px">ABOUT US</a>
    <a href="#" style="left:337px">AREAS OF PRACTICE</a>
    <a href="#" style="left:479px">RESOURCES</a>
    <a href="#" style="left:586px">BLOG</a>
    <a href="#" style="left:669px">FAQ</a>
    <a href="#" style="left:767px">CONTACT US</a>
  </nav>

  <aside class="panel info">
    <h2>IMPORTANT INFORMATION</h2>
    <h3>chapter 7</h3>
    <div class="photo" role="img" aria-label="Photo of a smiling family with children on bicycles"></div>
    <p>Often called the liquidation chapter, or “fresh start,” chapter 7 is used by individuals, families, partnerships, or corporations whose financial difficulties do not allow them to repay all of their debts.</p>
  </aside>

  <aside class="panel contact">
    <h2>CONTACT FORM</h2>
    <p class="req">Fields marked with * are required.</p>
    <span class="field first">Name *</span>
    <span class="field">Email *</span>
    <span class="field">Phone</span>
    <span class="field">Subject *</span>
    <span class="field msg">Message *</span>
    <span class="submit">SUBMIT</span>
  </aside>

  <section class="hero" role="img" aria-label="Photo of a confident attorney in a suit in front of a courthouse">
    <div class="hero-tag"><span class="a">Always Protecting</span><span class="b">CLIENT’S INTERESTS!</span></div>
    <div class="dots"><span></span><span></span><span></span></div>
  </section>

  <main class="main">
    <h1>Welcome to BK Law Desk - Complete Bankruptcy Information</h1>
    <p>Gravel_-_main_pageThe Law Offices of Marta K. Dolvenidze is a consumer law office dedicated to consumer protection and zealously defending the rights of our clients. We offer the big firm quality legal representation with a small firm individualized attention to each client.</p>
    <p>Our office offers services in: all types of consumer bankruptcy filings, i.e. Chapter 7, Chapter 13, Chapter 11, negotiating a settlement of your debts, assisting you in the defense of collection litigation and defending you against foreclosure. Please review our site and see what we may be able to offer you. Feel free to call us at (415) 555-0147 or use our free case evaluation form.</p>
    <h2>Speak to a Lawyer</h2>
    <p>Unlike some other law firms, when you call the Law Office of Marta K. Dolvenidze you will speak to an actual attorney. Not a paralegal or assistant. And even after retaining our office you will still speak to an attorney unlike other firms where you cannot get a hold of your attorney after several attempts.</p>
  </main>

  <article class="card" style="left:17px">
    <h2>Debt Relief</h2>
    <div class="photo" role="img" aria-label="Photo of a smiling couple"></div>
    <p>This page is available, however, but because occasionally circumstances occur in which toil and pain can procure him some great. To take a trivial example, which of us ever undertakes laborious physical exercise, except to obtain some advantage from it.</p>
    <span class="more">read more...</span>
  </article>
  <article class="card" style="left:307px">
    <h2 class="small">Foreclosure Prevention</h2>
    <div class="photo" role="img" aria-label="Photo of a smiling couple"></div>
    <p>This page is available, however, but because occasionally circumstances occur in which toil and pain can procure him some great. To take a trivial example, which of us ever undertakes laborious physical exercise, except to obtain some advantage from it.</p>
    <span class="more">read more...</span>
  </article>
  <article class="card" style="left:596px">
    <h2>Chapter 13</h2>
    <div class="photo" role="img" aria-label="Photo of a smiling couple"></div>
    <p>This page is available, however, but because occasionally circumstances occur in which toil and pain can procure him some great. To take a trivial example, which of us ever undertakes laborious physical exercise, except to obtain some advantage from it.</p>
    <span class="more">read more...</span>
  </article>

  <footer class="footer">
    <div class="links"><span>Go to top</span>Copyright © 2010 KDLaw. All Rights Reserved. | Web Development by Sitegrove</div>
    <p class="disclaimer">Disclaimer: The Law Offices of Marta K. Dolvenidze is a Debt Relief law firm as defined by 11 U.S.C. 528. We help people file for Bankruptcy Relief under the Bankruptcy Code. The information contained on this website is not to be construed as legal advice. It is not intended to solicit or form an attorney-client relationship. We do not guarantee any result and prior results do not guarantee a similar outcome. This is an attorney advertisement and this website is for informational purposes only.</p>
    <div class="badge" role="img" aria-label="Professional association membership badge"></div>
  </footer>
</div>
</body>
</html>
```